Brimsett Gardening Fresh New Website

We are looking to create a simple fresh website for our landscaping business. The website should appeal to a 'high end' audience. We deal with a lot of Embassies and affluent clients who have extremely large gardens that are meticulously maintained. The site is about communicating our excellent landscaping and customer service skills and encouraging new clients to reach out and engage us to take care of their gardens.

The website is basically going to be our business card, it will have almost no functionality other than two 'contact us' forms, one for smaller clients and one for more detailed projects.

The website will not have a lot of written content and will have to show photos of beautifully landscaped gardens.

The main logo in black will influence the site, however, we are open to all suggestions.

We are expecting to have the following pages:
Home Page
Services
About Us
Contact Us
Showcase (photo gallery of our work)

We need someone who can code it to wordpress and be available for minor changes over a number of days. They will be simple tweaks.

```html
<!DOCTYPE html>
<html lang="en">
<head>
<meta charset="utf-8">
<title>Brimsett Gardening</title>
<link rel="stylesheet" href="https://fonts.googleapis.com/css2?family=Gelasio:wght@500;600&family=Lato:wght@400;700&display=swap">
<style>
:root{
  --gold-dark:#b1842a;
  --gold:#c9982e;
  --gold-light:#f6d84a;
  --ink:#111111;
  --text:#2b2b2b;
  --muted-bg:#f5f5f5;
  --footer:#1c1c1c;
  --white:#ffffff;
  --serif:'Gelasio', Georgia, serif;
  --sans:'Lato', Arial, sans-serif;
}
*{box-sizing:border-box;margin:0;padding:0}
html,body{width:1200px;height:4132px;overflow:hidden}
body{position:relative;font-family:var(--sans);color:var(--text);background:var(--white)}
.abs{position:absolute}
.btn{position:absolute;display:flex;align-items:center;justify-content:center;font:700 12px var(--sans);color:#1a1a1a;background:linear-gradient(90deg,var(--gold-dark),var(--gold-light))}
.section-title{position:absolute;left:0;width:1200px;text-align:center;font:600 36px/1 var(--serif);color:var(--ink)}
.section-title span{color:var(--gold)}
.photo{position:absolute}

/* Hero */
.hero{position:absolute;left:0;top:0;width:1200px;height:589px;background:linear-gradient(180deg,#8f979b 0%,#7d8783 38%,#5f7242 62%,#4d6a22 80%,#3f5a1b 100%)}
.hero-shade{position:absolute;inset:0;background:linear-gradient(90deg,rgba(0,0,0,.35),rgba(0,0,0,.05) 70%)}
.brand{position:absolute;left:141px;top:10px;width:110px;text-align:center;color:var(--white);font-family:var(--serif);font-weight:500}
.brand .dot{width:22px;height:22px;border:1.5px solid var(--white);border-radius:50%;margin:0 auto 24px}
.brand .name{font-size:14px;letter-spacing:5px;display:block}
.brand .sub{font-size:8px;letter-spacing:4px;display:block;margin-top:3px}
.top-quote{left:906px;top:21px;width:151px;height:34px;background:#0d0d0d;color:var(--white);gap:10px}
.nav-line{position:absolute;left:536px;top:71px;width:521px;height:1px;background:rgba(255,255,255,.5)}
.nav a{position:absolute;top:83px;font:400 12px var(--sans);color:var(--white);text-decoration:none}
.follow{position:absolute;left:52px;top:178px;font:700 11px var(--sans);color:var(--white);writing-mode:vertical-rl;letter-spacing:1px}
.social-dot{position:absolute;left:54px;width:18px;height:18px;border:1.6px solid var(--white);border-radius:50%}
.eyebrow{position:absolute;left:141px;top:256px;font:500 22px var(--sans);letter-spacing:2px;color:var(--white)}
.hero-title{position:absolute;left:141px;top:292px;font:600 38px/1 var(--serif);color:var(--white)}
.quote-panel{position:absolute;left:701px;top:135px;width:356px;height:431px;background:rgba(245,245,245,.86)}
.quote-panel h2{position:absolute;left:16px;top:20px;font:500 21px/27px var(--serif);color:var(--ink)}
.field{position:absolute;left:21px;width:314px;height:32px;background:rgba(228,228,228,.9);font:400 12px var(--sans);color:#222;padding:0 14px;display:flex;align-items:center}
.field b{color:#c0392b;font-weight:400}
.field.select{justify-content:space-between}

/* Services */
.card{position:absolute;top:714px;width:290px;height:314px;background:var(--white);box-shadow:0 8px 22px rgba(0,0,0,.1)}
.card .photo{left:0;top:0;width:290px;height:171px}
.card .badge{position:absolute;left:107px;top:130px;width:76px;height:76px;border-radius:50%;background:var(--white);display:flex;align-items:center;justify-content:center}
.card h3{position:absolute;left:0;top:200px;width:100%;text-align:center;font:600 18px var(--serif);color:var(--ink)}
.card p{position:absolute;left:20px;top:233px;width:250px;text-align:center;font:400 12px/22.5px var(--sans);color:#222}

/* About */
.about{position:absolute;left:0;top:1184px;width:1200px;height:508px;background:var(--muted-bg)}
.about h2{position:absolute;left:141px;top:100px;font:600 38px/45px var(--serif);color:var(--ink)}
.about h2 span{color:var(--gold)}
.about p{position:absolute;left:141px;width:445px;font:400 12px/22.5px var(--sans);color:#222}
.about .frame{position:absolute;left:659px;top:85px;width:398px;height:322px;border:3px solid var(--gold-dark)}

/* Reviews */
.review-back{position:absolute;left:310px;top:1890px;width:578px;height:182px;background:var(--white);box-shadow:0 10px 24px rgba(0,0,0,.08)}
.review{position:absolute;left:282px;top:1872px;width:634px;height:183px;background:var(--white);box-shadow:0 6px 20px rgba(0,0,0,.08)}
.quote-badge{position:absolute;left:288px;top:-29px;width:58px;height:58px;border-radius:50%;background:linear-gradient(135deg,var(--gold-dark),var(--gold-light));display:flex;align-items:center;justify-content:center;font:700 40px/1 var(--serif);color:#111;padding-top:16px}
.review p{position:absolute;left:55px;top:42px;width:524px;text-align:center;font:400 12px/22.5px var(--sans);color:#222}
.review .who{position:absolute;top:115px;width:100%;text-align:center;font:700 13px var(--sans);color:#111}

/* Banner */
.banner{position:absolute;left:0;top:2156px;width:1200px;height:431px;background:radial-gradient(ellipse at 50% 50%,#4e5e2a,#2f3d18 70%,#24310f)}
.banner::after{content:"";position:absolute;inset:0;background:rgba(0,0,0,.35)}
.banner-content{position:absolute;left:0;top:0;width:1200px;height:431px;z-index:1}
.banner h2{position:absolute;left:0;top:138px;width:100%;text-align:center;font:600 38px var(--serif);color:var(--white)}
.banner p{position:absolute;left:210px;top:191px;width:780px;text-align:center;font:400 12px/22.5px var(--sans);color:var(--white)}

/* Gallery */
.tile{position:absolute;width:291px;height:217px}
.tile-text{position:absolute;inset:0;display:flex;flex-direction:column;align-items:center;justify-content:center;color:var(--white);text-align:center;padding:0 18px}
.tile-text h3{font:600 18px var(--serif);margin-bottom:12px}
.tile-text p{font:400 12px/22.5px var(--sans)}

/* Inquiry */
.inquiry{position:absolute;left:0;top:3340px;width:1200px;height:465px;background:var(--muted-bg)}
.in-field{position:absolute;height:31px;background:var(--white);font:400 12px var(--sans);color:#222;padding:0 18px;display:flex;align-items:center}

/* Footer */
.footer{position:absolute;left:0;top:3805px;width:1200px;height:292px;background:var(--footer);color:var(--white)}
.foot-brand{position:absolute;left:141px;width:148px;text-align:center;font-family:var(--serif);font-weight:500;color:var(--gold)}
.foot-brand .dot{width:30px;height:30px;border:2px solid var(--gold);border-radius:50%;margin:0 auto 22px}
.foot-brand .name{display:block;font-size:20px;letter-spacing:8px}
.foot-brand .sub{display:block;font-size:10px;letter-spacing:7px;margin-top:4px}
.footer h4{position:absolute;top:64px;font:700 13px var(--sans)}
.footer .link{position:absolute;left:414px;font:400 12px var(--sans)}
.ic{position:absolute;width:36px;height:36px;border-radius:50%;background:linear-gradient(135deg,var(--gold-dark),var(--gold-light));display:flex;align-items:center;justify-content:center}
.footer .txt{position:absolute;font:400 12px/15px var(--sans)}
.copy{position:absolute;left:0;top:4097px;width:1200px;height:35px;background:linear-gradient(90deg,var(--gold-dark),var(--gold-light));display:flex;align-items:center;justify-content:center;font:400 12px var(--sans);color:#1a1a1a}
</style>
</head>
<body>

<!-- Hero -->
<header class="hero">
  <div class="photo" role="img" aria-label="Wide lawn in front of modern city buildings under an overcast sky" style="inset:0;background:inherit"></div>
  <div class="hero-shade"></div>
  <div class="brand"><div class="dot"></div><span class="name">BRIMSETT</span><span class="sub">GARDENING</span></div>
  <div class="btn top-quote">Request A Quote
    <svg width="12" height="8" viewBox="0 0 12 8"><path d="M1 1l5 5 5-5" stroke="#fff" stroke-width="1.6" fill="none"/></svg>
  </div>
  <div class="nav-line"></div>
  <nav class="nav">
    <a style="left:536px">Home</a><a style="left:642px">Services</a><a style="left:762px">Gallery</a><a style="left:873px">About Us</a><a style="left:996px">Contact Us</a>
  </nav>
  <div class="follow">Follow Us</div>
  <div class="social-dot" style="top:262px"></div>
  <div class="social-dot" style="top:300px"></div>
  <div class="social-dot" style="top:339px"></div>
  <div class="eyebrow">LANDSCAPE PROS</div>
  <h1 class="hero-title">Elegance In Every Landscape</h1>
  <div class="btn" style="left:141px;top:358px;width:132px;height:32px">Request A Quote</div>

  <form class="quote-panel">
    <h2>24% Off For New<br>Landscape Services</h2>
    <div class="field" style="top:86px">Name<b>*</b></div>
    <div class="field" style="top:128px">Email<b>*</b></div>
    <div class="field" style="top:170px">Phone Number<b>*</b></div>
    <div class="field" style="top:213px">Street Address &amp; Zip Code<b>*</b></div>
    <div class="field select" style="top:255px">Which Service Would You Like A Bill For?
      <svg width="12" height="8" viewBox="0 0 12 8"><path d="M1 1l5 5 5-5" stroke="#111" stroke-width="1.6" fill="none"/></svg>
    </div>
    <div class="field" style="top:298px;height:67px;align-items:flex-start;padding-top:10px">Message</div>
    <div class="btn" style="left:21px;top:375px;width:314px;height:32px">Request A Quote</div>
  </form>
</header>

<!-- Services -->
<h2 class="section-title" style="top:646px">Our <span>Services</span></h2>
<article class="card" style="left:141px">
  <div class="photo" role="img" aria-label="Flowering garden beds and bright green lawn" style="background:linear-gradient(180deg,#6f9a3f,#c0466a 45%,#4fa52c 65%,#59b92f)"></div>
  <div class="badge"><svg width="40" height="30" viewBox="0 0 40 30"><path d="M4 24 L8 8 M12 24 L14 4 M20 24 L20 6 M28 24 L26 4 M36 24 L32 8" stroke="#b1842a" stroke-width="2" fill="none"/><rect x="4" y="23" width="32" height="5" fill="none" stroke="#333" stroke-width="1.4"/></svg></div>
  <h3>Lawn Fertilizing</h3>
  <p>Lorem Ipsum Is Simply Dummy Text Of The Printing And Typesetting Industry. Contrary Belief, Lorem Ipsum &nbsp; Random Text.</p>
</article>
<article class="card" style="left:454px">
  <div class="photo" role="img" aria-label="Aerial view of a paved patio with trees and seating" style="background:linear-gradient(160deg,#7e8b86,#a7aba3 45%,#4f6b3d 80%,#6b7a68)"></div>
  <div class="badge"><svg width="34" height="34" viewBox="0 0 34 34"><g fill="none" stroke="#444" stroke-width="1.6"><rect x="4" y="4" width="11" height="11"/><rect x="19" y="4" width="11" height="11"/><rect x="4" y="19" width="11" height="11"/><rect x="19" y="19" width="11" height="11"/></g></svg></div>
  <h3>Patios</h3>
  <p>Lorem Ipsum Is Simply Dummy Text Of The Printing And Typesetting Industry. Contrary Belief, Lorem Ipsum &nbsp; Random Text.</p>
</article>
<article class="card" style="left:767px">
  <div class="photo" role="img" aria-label="Gardener spraying leafy green plants" style="background:linear-gradient(120deg,#3f6e2a,#7fa55a 50%,#2e4a7a 85%,#1f3468)"></div>
  <div class="badge"><svg width="36" height="34" viewBox="0 0 36 34"><path d="M18 30 V6 M18 20 L6 12 M18 20 L30 12 M18 25 L9 22 M18 25 L27 22" stroke="#444" stroke-width="1.6" fill="none"/><circle cx="28" cy="27" r="4" fill="none" stroke="#b1842a" stroke-width="1.6"/></svg></div>
  <h3>Weed Control</h3>
  <p>Lorem Ipsum Is Simply Dummy Text Of The Printing And Typesetting Industry. Contrary Belief, Lorem Ipsum &nbsp; Random Text.</p>
</article>
<div class="btn" style="left:534px;top:1065px;width:132px;height:34px">Request A Quote</div>

<!-- About -->
<section class="about">
  <h2>About<br><span>Brimsett Gardening</span></h2>
  <p style="top:198px">Lorem Ipsum Is Simply Dummy Text Of The Printing And Typesetting Industry. Lorem Ipsum Has Been The Industry's Standard Dummy Text Ever Since The 1500s, When An Unknown Printer Took A Galley Of Type And Scrambled It To Make A Type Specimen Book.</p>
  <p style="top:294px">Lorem Ipsum Is Simply Dummy Text Of The Printing And Typesetting Industry. Lorem Ipsum Has Been The Industry's Standard Dummy Text Ever Since The 1500s, When &nbsp;And Scrambled It To Make A Type Specimen Book.</p>
  <div class="btn" style="left:141px;top:377px;width:93px;height:34px">Read More</div>
  <div class="frame"></div>
  <div class="photo" role="img" aria-label="Glass office building with a tree and flower bed at its entrance" style="left:645px;top:99px;width:399px;height:324px;background:linear-gradient(180deg,#9eaab2,#6f7e86 40%,#4c6b34 70%,#6c3f8a 85%,#3f7a2a)"></div>
</section>

<!-- Reviews -->
<h2 class="section-title" style="top:1772px">Customer <span>Reviews</span></h2>
<div class="review-back"></div>
<div class="review">
  <div class="quote-badge">&ldquo;</div>
  <p>Lorem Ipsum Is Simply Dummy Text Of The Printing And Typesetting Industry. Lorem Ipsum Has Been The Industry's Standard Dummy Text Ever Since The 1500s, When An Unknown Printer Took A Galley Of Type And Scrambled It To Make A Type Specimen Book.</p>
  <div class="who">&ndash; Daniel. R</div>
  <svg class="abs" style="left:294px;top:146px" width="46" height="12" viewBox="0 0 46 12"><path d="M18 6H2M7 1L2 6l5 5" stroke="#111" stroke-width="1.5" fill="none"/><path d="M28 6h16M39 1l5 5-5 5" stroke="#b1842a" stroke-width="1.5" fill="none"/></svg>
</div>

<!-- Banner -->
<section class="banner" role="img" aria-label="Aerial view of a mower cutting a lawn beside a winding stone path">
  <div class="banner-content">
    <h2>Build Your Outdoor Dream With Us</h2>
    <p>Lorem Ipsum Is Simply Dummy Text Of The Printing And Typesetting Industry. Lorem Ipsum Has Been The Industry's Standard Dummy Text Ever Since The 1500s, When An Unknown Printer Took A Galley Of Type And Scrambled It To Make A Type Specimen Book.</p>
    <div class="btn" style="left:552px;top:255px;width:96px;height:32px">Contact Us</div>
  </div>
</section>

<!-- Gallery -->
<h2 class="section-title" style="top:2671px">Work <span>Gallery</span></h2>
<div class="tile" role="img" aria-label="Golf green framed by pine trees" style="left:141px;top:2738px;background:linear-gradient(180deg,#a9b3a8,#3f5a33 40%,#6aa13a 70%,#4e8a2a)"></div>
<div class="tile" role="img" aria-label="Close-up of blades of grass" style="left:454px;top:2738px;background:radial-gradient(circle at 50% 50%,#9ec26a,#5f8c33 60%,#3b5e22)"></div>
<div class="tile" role="img" aria-label="Round hay bale on a lawn" style="left:767px;top:2738px;background:linear-gradient(180deg,#8c9a4a,#6f7b3e 50%,#8a8e52)"></div>
<div class="tile" role="img" aria-label="Worker rolling out fresh turf" style="left:141px;top:2977px;background:linear-gradient(160deg,#2d4a7a,#5e8a3a 40%,#7a6a52 70%,#5b4a3a)"></div>
<div class="tile" role="img" aria-label="Garden with flowering shrubs" style="left:454px;top:2977px;background:linear-gradient(180deg,#3c3a2c,#4a2e2a 50%,#2f3a22)">
  <div class="tile-text" style="background:rgba(0,0,0,.35)"><h3>Lorem Ipsum &nbsp;Text</h3><p>Lorem Ipsum Has Been The Industry's Standard Dummy Text Ever Since The 1500s, When An &nbsp;Galley Of Type And Scrambled It To Make A Type Specimen Book.</p></div>
</div>
<div class="tile" role="img" aria-label="Brick path curving through a tree-lined park" style="left:767px;top:2977px;background:linear-gradient(180deg,#c9d9e8,#4f8a2e 35%,#6aa83a 60%,#a2645a 80%,#5f9a34)"></div>
<div class="btn" style="left:552px;top:3221px;width:96px;height:34px">Contact Us</div>

<!-- Quick Inquiry -->
<section class="inquiry">
  <h2 class="section-title" style="top:84px">Quick <span>Inquiry</span></h2>
  <div class="in-field" style="left:289px;top:160px;width:303px">First Name*</div>
  <div class="in-field" style="left:606px;top:160px;width:304px">Last Name*</div>
  <div class="in-field" style="left:289px;top:205px;width:303px">Email*</div>
  <div class="in-field" style="left:606px;top:205px;width:304px">Phone Number*</div>
  <div class="in-field" style="left:289px;top:251px;width:621px;height:82px;align-items:flex-start;padding-top:10px">Message</div>
  <div class="btn" style="left:289px;top:349px;width:621px;height:31px">Submit</div>
</section>

<!-- Footer -->
<footer class="footer">
  <div class="foot-brand" style="top:78px"><div class="dot"></div><span class="name">BRIMSETT</span><span class="sub">GARDENING</span></div>

  <h4 style="left:414px">Quick Links</h4>
  <span class="link" style="top:94px">Home</span>
  <span class="link" style="top:120px">Services</span>
  <span class="link" style="top:145px">Gallery</span>
  <span class="link" style="top:171px">About Us</span>
  <span class="link" style="top:197px">FAQs</span>
  <span class="link" style="top:222px">Contact Us</span>

  <h4 style="left:616px">Contact Details</h4>
  <div class="ic" style="left:616px;top:94px"><svg width="16" height="18" viewBox="0 0 16 18"><path d="M8 17s6-6 6-10A6 6 0 0 0 2 7c0 4 6 10 6 10z" fill="none" stroke="#111" stroke-width="1.5"/><circle cx="8" cy="7" r="2" fill="none" stroke="#111" stroke-width="1.5"/></svg></div>
  <div class="txt" style="left:666px;top:98px">123, Street Name, City<br>Name, Country Name, &nbsp;1234</div>
  <div class="ic" style="left:616px;top:142px"><svg width="16" height="16" viewBox="0 0 16 16"><path d="M3 1.5h3l1.5 3.5-2 1.3a9 9 0 0 0 4.2 4.2l1.3-2 3.5 1.5v3A1.5 1.5 0 0 1 13 15 12 12 0 0 1 1 3a1.5 1.5 0 0 1 2-1.5z" fill="none" stroke="#111" stroke-width="1.4"/></svg></div>
  <div class="txt" style="left:666px;top:153px">123 456 7890</div>
  <div class="ic" style="left:616px;top:192px"><svg width="16" height="12" viewBox="0 0 16 12"><rect x="1" y="1" width="14" height="10" fill="none" stroke="#111" stroke-width="1.4"/><path d="M1 1l7 6 7-6" fill="none" stroke="#111" stroke-width="1.4"/></svg></div>
  <div class="txt" style="left:666px;top:203px">brimsettgardening@example.com</div>

  <h4 style="left:951px">Follow Us</h4>
  <div class="ic" style="left:951px;top:94px"><span style="width:14px;height:14px;border:1.5px solid #111;border-radius:50%"></span></div>
  <div class="txt" style="left:1000px;top:105px">Community</div>
  <div class="ic" style="left:951px;top:142px"><span style="width:14px;height:14px;border:1.5px solid #111;border-radius:50%"></span></div>
  <div class="txt" style="left:1000px;top:153px">Photo Feed</div>
  <div class="ic" style="left:951px;top:192px"><span style="width:14px;height:14px;border:1.5px solid #111;border-radius:50%"></span></div>
  <div class="txt" style="left:1000px;top:203px">Careers</div>
</footer>
<div class="copy">&copy; 2024 Brimsett Gardening. All Rights Reserved.</div>

</body>
</html>
```